New Bicycle shop business card

Hi!
I'm looking for a business card for my new proffesional bike mechanics shop. This shop is only for fixing broken bikes and not selling bikes.
Peferbly a modern and sleek and modern design.
Colors: black, grey, red, white
Information:
Name: Rijwielwerkplaats Vanhoutte
Shop owner: Bart Vanhoutte & Marieke Segers
Website: www.rijwielwerkplaats-vanhoutte.be
Email: info@rijwielwerkplaats-vanhoutte.be
Phone number: +32471902368
Street adres: Kerkweg 46
9940 Bellebeke
Slogan/shop information: Herstellingen van alle merken.
Logo: see files.
Target Market(s)
People who seek a mechanic to fix or upgrade their bikes.
Contact Information for Business Card
Information:
Website: info@rijwielwerkplaats-vanhoutte.be
9940 Bellebeke
Logo: see files.

```html
<!DOCTYPE html>
<html lang="nl">
<head>
<meta charset="utf-8">
<title>Rijwielwerkplaats Vanhoutte – visitekaartje</title>
<link rel="stylesheet" href="https://fonts.googleapis.com/css2?family=Montserrat:wght@700&family=Roboto:wght@400;700&display=swap">
<style>
  :root {
    --backdrop: #e4e4e4;
    --card: #fbfbfb;
    --ink: #1e1e1e;
    --ink-soft: #3a3a3a;
    --red: #d9283b;
    --grey: #9a9a9a;
    --grey-faint: #ececec;
  }
  * { box-sizing: border-box; margin: 0; padding: 0; }
  html, body { width: 1200px; height: 852px; overflow: hidden; }
  body {
    background: var(--backdrop);
    font-family: "Roboto", Arial, sans-serif;
    color: var(--ink);
    display: flex;
    align-items: center;
    justify-content: center;
    gap: 40px;
  }
  .card {
    position: relative;
    width: 540px;
    height: 309px;
    background: var(--card);
    border-radius: 18px;
    overflow: hidden;
    box-shadow: 0 8px 22px rgba(0,0,0,.18);
  }
  .brand {
    display: flex;
    align-items: center;
    gap: 12px;
  }
  .brand-mark {
    width: 22px;
    height: 22px;
    background: var(--red);
    flex: none;
  }
  .brand-name {
    font-family: "Roboto", Arial, sans-serif;
    font-weight: 700;
    color: var(--ink);
    text-transform: uppercase;
    letter-spacing: .06em;
    line-height: 1.1;
  }

  /* Front */
  .card-front .brand {
    position: absolute;
    left: 0; right: 0; top: 92px;
    justify-content: center;
  }
  .card-front .brand-name { font-size: 25px; }
  .tagline {
    position: absolute;
    left: 0; right: 0; top: 214px;
    display: flex;
    align-items: center;
    justify-content: center;
    gap: 14px;
    font-size: 13px;
    color: var(--ink-soft);
  }
  .tagline-rule { width: 46px; height: 2px; background: var(--red); }
  .front-band { position: absolute; left: 0; bottom: 0; width: 100%; height: 14px; }

  /* Back */
  .back-deco {
    position: absolute;
    right: -40px; top: -30px;
    width: 300px; height: 300px;
    border-radius: 50%;
    background: var(--grey-faint);
  }
  .card-back .brand {
    position: absolute;
    left: 34px; top: 40px;
  }
  .card-back .brand-name { font-size: 19px; }
  .person { position: absolute; left: 34px; top: 150px; }
  .person-name {
    font-family: "Montserrat", Arial, sans-serif;
    font-weight: 700;
    font-size: 19px;
    color: var(--red);
    text-transform: uppercase;
    letter-spacing: .04em;
  }
  .person-role { font-size: 13px; color: var(--ink-soft); margin-top: 2px; }
  .address {
    position: absolute; left: 34px; top: 232px;
    font-style: normal;
    font-size: 14px;
    line-height: 1.45;
    color: var(--ink-soft);
  }
  .contact {
    position: absolute; left: 280px; top: 104px;
    list-style: none;
    font-size: 12.5px;
    color: var(--ink-soft);
  }
  .contact li { display: flex; align-items: center; gap: 9px; line-height: 21px; }
  .contact svg { width: 12px; height: 12px; fill: var(--red); flex: none; }
  .slogan-tab {
    position: absolute;
    right: 0; bottom: 0;
    width: 260px; height: 56px;
    background: var(--red);
    border-top-left-radius: 14px;
    color: #fff;
    font-size: 13.5px;
    display: flex; align-items: center; justify-content: center;
  }
  .back-strip {
    position: absolute; left: 0; bottom: 0;
    width: 280px; height: 6px;
    background: var(--grey);
    opacity: .35;
  }
</style>
</head>
<body>

  <section class="card card-front" aria-label="Voorkant visitekaartje">
    <div class="brand">
      <span class="brand-mark"></span>
      <span class="brand-name">Rijwielwerkplaats<br>Vanhoutte</span>
    </div>
    <p class="tagline">
      <span class="tagline-rule"></span>
      Herstellingen van alle merken
      <span class="tagline-rule"></span>
    </p>
    <svg class="front-band" viewBox="0 0 540 14" preserveAspectRatio="none" aria-hidden="true">
      <rect x="0" y="0" width="540" height="14" fill="#b5b5b5"/>
      <polygon points="0,0 300,0 280,14 0,14" fill="#d9283b"/>
    </svg>
  </section>

  <section class="card card-back" aria-label="Achterkant visitekaartje">
    <div class="back-deco" aria-hidden="true"></div>
    <div class="brand">
      <span class="brand-mark"></span>
      <span class="brand-name">Rijwielwerkplaats<br>Vanhoutte</span>
    </div>

    <ul class="contact">
      <li>
        <svg viewBox="0 0 24 24" aria-hidden="true"><path d="M6.6 10.8a15.1 15.1 0 0 0 6.6 6.6l2.2-2.2a1 1 0 0 1 1-.25 11.4 11.4 0 0 0 3.6.57 1 1 0 0 1 1 1V20a1 1 0 0 1-1 1A17 17 0 0 1 3 4a1 1 0 0 1 1-1h3.5a1 1 0 0 1 1 1c0 1.25.2 2.45.57 3.57a1 1 0 0 1-.25 1z"/></svg>
        +32471902368
      </li>
      <li>
        <svg viewBox="0 0 24 24" aria-hidden="true"><path d="M12 2a10 10 0 1 0 0 20 10 10 0 0 0 0-20zm6.9 6h-2.9a15.7 15.7 0 0 0-1.4-3.6A8 8 0 0 1 18.9 8zM12 4a14 14 0 0 1 1.9 4h-3.8A14 14 0 0 1 12 4zM4.3 14a8 8 0 0 1 0-4h3.4a16.5 16.5 0 0 0 0 4zm.8 2h2.9a15.7 15.7 0 0 0 1.4 3.6A8 8 0 0 1 5.1 16zM8 8H5.1a8 8 0 0 1 4.3-3.6A15.7 15.7 0 0 0 8 8zm4 12a14 14 0 0 1-1.9-4h3.8A14 14 0 0 1 12 20zm2.3-6H9.7a14.7 14.7 0 0 1 0-4h4.6a14.7 14.7 0 0 1 0 4zm.3 5.6a15.7 15.7 0 0 0 1.4-3.6h2.9a8 8 0 0 1-4.3 3.6zm1.7-5.6a16.5 16.5 0 0 0 0-4h3.4a8 8 0 0 1 0 4z"/></svg>
        www.rijwielwerkplaats-vanhoutte.be
      </li>
      <li>
        <svg viewBox="0 0 24 24" aria-hidden="true"><path d="M2 5h20v14H2zm2 2v.5l8 5 8-5V7zm0 2.8V17h16V9.8l-8 5z"/></svg>
        info@rijwielwerkplaats-vanhoutte.be
      </li>
    </ul>

    <div class="person">
      <p class="person-name">Marieke Segers</p>
      <p class="person-role">Owner</p>
    </div>
    <address class="address">
      Kerkweg 46<br>
      9940 Bellebeke
    </address>

    <div class="back-strip" aria-hidden="true"></div>
    <p class="slogan-tab">Herstellingen van alle merken</p>
  </section>

</body>
</html>
```